We are having a Bold Stride Makeover Challenge at our fitness studio. We need a poster design using the template attached as a reference. I have also included our Vornalux logo to put on the poster. Please DO NOT use the graphics in the flyer as we are expecting something much better :-)

-Size needed 11x17 with bleeding for printing

-We need this made in Photoshop (CS3 friendly) or at least delivered in PS as we might change some text or re-arrange the design later on.

-We need this in layers.

```html
<!DOCTYPE html>
<html lang="en">
<head>
<meta charset="utf-8">
<title>Vornalux Bootcamps – Bold Stride Makeover Challenge</title>
<link rel="stylesheet" href="https://fonts.googleapis.com/css2?family=Old+Standard+TT:wght@400;700&family=PT+Sans&family=Rokkitt:wght@700;800&family=Varela+Round&display=swap">
<style>
  :root {
    --paper: #c9cdd0;
    --panel: #a9b7c2;
    --frame: #b8712f;
    --ink: #1c1c1c;
    --label-blue: #3b3ff0;
    --date-blue: #2f34e6;
    --highlight: #ffff00;
    --wood-light: #e0a23a;
    --wood-dark: #9a5a1c;
    --url-orange: #c8782c;
  }
  * { margin: 0; padding: 0; box-sizing: border-box; }
  html, body { width: 777px; height: 1200px; overflow: hidden; background: var(--paper); }
  .poster { position: relative; width: 777px; height: 1200px; background: var(--paper); overflow: hidden; }
  .frame { position: absolute; inset: 0; }
  .corner-ornament { position: absolute; width: 64px; height: 64px; background: var(--frame); border-radius: 50%; opacity: .85; }
  .corner-ornament.tl { left: 14px; top: 22px; }
  .corner-ornament.tr { right: 14px; top: 22px; }
  .corner-ornament.bl { left: 14px; bottom: 18px; }
  .corner-ornament.br { right: 14px; bottom: 18px; }
  .hero-photo {
    position: absolute; left: 104px; top: 224px; width: 620px; height: 760px;
    background: radial-gradient(ellipse at 50% 45%, #8f9fad 0%, #9eadb9 45%, rgba(169,183,194,0) 75%);
  }
  .brand {
    position: absolute; left: 146px; top: 62px; width: 488px; height: 160px;
    display: flex; align-items: center; justify-content: center;
    font-family: "Rokkitt", serif; font-weight: 800; font-size: 54px; color: var(--ink);
    letter-spacing: 1px; text-transform: uppercase;
  }
  .headline {
    position: absolute; left: 0; width: 777px; top: 358px; text-align: center;
    font-family: "Old Standard TT", serif; font-weight: 700; font-size: 44px; line-height: 58px;
    color: #2a2a2a; text-transform: uppercase; letter-spacing: .5px;
  }
  .subhead {
    position: absolute; left: 0; width: 777px; top: 480px; text-align: center;
    font-family: "PT Sans", sans-serif; font-size: 30px; line-height: 46px; color: var(--ink);
  }
  .label {
    position: absolute; font-family: "Rokkitt", serif; font-weight: 800; font-size: 31px;
    color: var(--label-blue); white-space: nowrap;
  }
  .label.kickoff { left: 56px; top: 638px; }
  .label.start { right: 485px; top: 698px; }
  .label.end { right: 493px; top: 758px; }
  .date {
    position: absolute; left: 334px; height: 37px; background: var(--highlight);
    font-family: "Varela Round", sans-serif; font-size: 27px; line-height: 37px;
    color: var(--date-blue); padding-left: 12px; white-space: nowrap;
  }
  .date.kickoff { top: 642px; width: 398px; }
  .date.start { top: 718px; width: 362px; }
  .date.end { top: 793px; width: 324px; }
  .offer {
    position: absolute; left: 48px; top: 876px; font-family: "Rokkitt", serif; font-weight: 800;
    font-size: 40px; line-height: 50px; color: var(--ink);
  }
  .prize-band {
    position: absolute; left: 40px; top: 986px; width: 694px; height: 76px;
    background: linear-gradient(180deg, var(--wood-dark) 0%, var(--wood-light) 35%, var(--wood-light) 65%, var(--wood-dark) 100%);
    border: 1px solid #3a2410;
    display: flex; align-items: center; justify-content: center;
    font-family: "Old Standard TT", serif; font-size: 44px; color: #3a2612;
  }
  .visit {
    position: absolute; left: 132px; top: 1080px; font-family: "Old Standard TT", serif;
    font-size: 32px; color: #3a3a3a;
  }
  .url {
    position: absolute; left: 132px; top: 1118px; font-family: "Rokkitt", serif; font-weight: 800;
    font-size: 33px; color: var(--url-orange);
  }
</style>
</head>
<body>
<main class="poster">
  <svg class="frame" width="777" height="1200" viewBox="0 0 777 1200">
    <path d="M94 22 H683 A80 80 0 0 0 763 102 V1102 A80 80 0 0 0 683 1182 H94 A80 80 0 0 0 14 1102 V102 A80 80 0 0 0 94 22 Z" fill="none" stroke="var(--frame)" stroke-width="3"/>
    <path d="M108 44 H669 A70 70 0 0 0 740 114 V1090 A70 70 0 0 0 669 1160 H108 A70 70 0 0 0 38 1090 V114 A70 70 0 0 0 108 44 Z" fill="var(--panel)"/>
  </svg>
  <div class="corner-ornament tl" role="img" aria-label="Decorative floral corner ornament"></div>
  <div class="corner-ornament tr" role="img" aria-label="Decorative floral corner ornament"></div>
  <div class="corner-ornament bl" role="img" aria-label="Decorative floral corner ornament"></div>
  <div class="corner-ornament br" role="img" aria-label="Decorative floral corner ornament"></div>

  <div class="hero-photo" role="img" aria-label="Faded photo of a fit athletic torso in jeans"></div>

  <div class="brand">Vornalux Bootcamps</div>

  <h1 class="headline">Bold Stride Makeover<br>Challenge</h1>
  <p class="subhead">In Just 6 Weeks, Transform Your Body And Get<br>In The Best Shape Of Your Life!</p>

  <span class="label kickoff">Kick Off Meeting:</span>
  <span class="date kickoff">Thursday, Jan 14 at 7:30 pm</span>
  <span class="label start">Start Date:</span>
  <span class="date start">Monday, January 18th</span>
  <span class="label end">End Date:</span>
  <span class="date end">Friday, February 26th</span>

  <p class="offer">6 Weeks of Training, Nutrition, and<br>Coaching Starting at just $99!</p>

  <div class="prize-band">$500 CASH Prize for Winner!</div>

  <p class="visit">Visit: FOR MORE INFO</p>
  <p class="url">www.vornaluxbootcamps.com</p>
</main>
</body>
</html>
```